Professional Package for CPA Firm

We would like a stationery design for our new CPA Firm based in Atlanta, GA called 'Vale 8'. We work with investors to help grow investments, tax free. We would like the design to have a professional/minimal look with a 'wow' factor. We need 9.5″ x 4.125″, 9x12, and 10x13 mailing envelopes, business cards, and a letterhead. We have a logo that is already complete. For the letterhead, we would like to have space to put credentials at the bottom of the page

Industry/Entity Type

CPA, Accounting

```html
<!DOCTYPE html>
<html lang="en">
<head>
<meta charset="utf-8">
<title>Vale 8 Stationery</title>
<link rel="stylesheet" href="https://fonts.googleapis.com/css2?family=Montserrat:wght@700&family=Open+Sans:wght@400;600&family=Great+Vibes&family=Lato:wght@400&display=swap">
<style>
:root{
  --stage:#959595;
  --paper:#ffffff;
  --ink:#000000;
  --text:#444444;
  --body:#7a7a7a;
  --blue:#0a9ddb;
  --blue-soft:#e3f3fb;
  --dark-accent:#0b1a22;
}
*{margin:0;padding:0;box-sizing:border-box}
html,body{width:1200px;height:680px;overflow:hidden}
body{background:var(--stage);position:relative;font-family:"Open Sans",sans-serif;color:var(--text)}
.piece{position:absolute;background:var(--paper);overflow:hidden}
.label{position:absolute;font-family:"Lato",sans-serif;font-size:9.5px;color:#111;letter-spacing:.2px;text-align:center;width:200px;transform:translateX(-50%)}
.brand-name{font-family:"Montserrat",sans-serif;font-weight:700;color:#fff;letter-spacing:.5px;white-space:nowrap}
.script{font-family:"Great Vibes",cursive;white-space:nowrap}
.pennant{position:absolute;display:flex;align-items:center;justify-content:center}
.pennant svg.shape{position:absolute;inset:0;width:100%;height:100%}
.pennant .brand-name{position:relative;margin-top:-14%}
.contact-list{list-style:none}
.contact-list li{display:flex;align-items:center;white-space:nowrap}
.icon{fill:var(--blue);flex:none}
.soft-fade{position:absolute;background:linear-gradient(135deg,rgba(227,243,251,0) 45%,var(--blue-soft) 100%)}
.dark-fade{position:absolute;background:linear-gradient(135deg,rgba(11,26,34,0) 50%,var(--dark-accent) 100%)}
/* letterhead */
.letterhead{left:67px;top:48px;width:390px;height:552px}
.letterhead .pennant{left:34px;top:-1px;width:89px;height:113px}
.letterhead .pennant .brand-name{font-size:15px}
.lh-address{position:absolute;left:280px;top:29px;font-size:6.6px;line-height:8.6px;color:#555}
.lh-address .contact-list{margin-top:3px}
.lh-address .icon{width:6px;height:6px;margin-right:4px}
.salutation{position:absolute;left:35px;top:154px;font-size:10px;color:#666}
.letter-body{position:absolute;left:35px;top:184px;width:324px;font-size:5.4px;line-height:8.5px;color:var(--body)}
.letter-body p{margin-bottom:8.5px;text-align:justify}
.signoff{position:absolute;left:35px;top:362px;font-size:5.4px;color:var(--body)}
.signature{position:absolute;left:32px;top:383px;width:72px;height:30px;background:linear-gradient(90deg,#c7dcef,#e8f1fa);border-radius:3px}
.letterhead .tagline{position:absolute;left:0;width:390px;top:510px;text-align:center;font-size:14px;color:#333}
/* envelope */
.env-back{left:490px;top:48px;width:354px;height:160px}
.env-flap{position:absolute;left:0;top:0;width:354px;height:58px}
.env-flap .tagline{position:absolute;left:0;width:354px;top:32px;text-align:center;font-size:9px;color:#fff}
.env-flap .brand-name{position:absolute;left:0;width:354px;top:13px;text-align:center;font-size:10px}
.env-front{left:543px;top:132px;width:356px;height:161px;box-shadow:0 1px 3px rgba(0,0,0,.25)}
.env-front .pennant{left:20px;top:0;width:71px;height:83px}
.env-front .pennant .brand-name{font-size:11px}
.env-address{position:absolute;left:20px;top:129px;font-size:7.2px;line-height:9px;color:#555}
/* cards */
.card-front{left:944px;top:48px;width:186px;height:106px}
.cf-info{position:absolute;left:44px;top:41px;display:flex;gap:5px}
.cf-name{text-align:right;font-size:3.6px;line-height:5px;color:#666;padding-right:5px;border-right:.5px solid #999}
.cf-name strong{display:block;font-size:5.6px;line-height:7px;color:var(--blue);font-weight:600}
.cf-info .contact-list{font-size:3.6px;line-height:5px;color:#666}
.cf-info .icon{width:3.5px;height:3.5px;margin-right:2px}
.card-back{left:944px;top:182px;width:193px;height:110px;background:var(--ink)}
.card-back .brand-name{position:absolute;left:0;width:193px;top:36px;text-align:center;font-size:17px}
.card-back .tagline{position:absolute;left:0;width:193px;top:84px;text-align:center;font-size:9px;color:#fff}
/* email signatures */
.sig{background:var(--ink);color:#fff}
.sig .name{font-weight:600;color:var(--blue);white-space:nowrap}
.sig .icon{margin-right:5px}
.sig-one{left:490px;top:334px;width:175px;height:266px}
.sig-one .brand-name{position:absolute;left:28px;top:68px;font-size:19px}
.sig-one .name{position:absolute;left:27px;top:108px;font-size:15px}
.sig-one .role{position:absolute;left:27px;top:127px;font-size:9px}
.sig-one .rule{position:absolute;left:28px;width:15px;height:.7px;background:var(--blue)}
.sig-one .addr{position:absolute;left:28px;top:154px;font-size:9px;line-height:11.5px}
.sig-one .contact-list{position:absolute;left:28px;top:195px;font-size:9px;line-height:11.5px}
.sig-one .icon{width:7px;height:7px}
.sig-two{left:695px;top:334px;width:455px;height:141px}
.sig-two .brand-name{position:absolute;left:38px;top:72px;font-size:19px}
.vr{position:absolute;width:.7px;background:#666}
.sig-two .name{position:absolute;left:162px;top:42px;font-size:15px}
.sig-two .role{position:absolute;left:162px;top:61px;font-size:9.5px}
.sig-two .addr{position:absolute;left:162px;top:73px;font-size:9.5px;line-height:11.5px}
.sig-two .contact-list{position:absolute;left:318px;top:52px;font-size:9.5px;line-height:11.5px}
.sig-two .icon{width:7px;height:7px}
.sig-three{left:695px;top:513px;width:455px;height:87px}
.sig-three .brand-name{position:absolute;left:18px;top:38px;font-size:15px}
.sig-three .who{position:absolute;left:115px;top:34px;width:104px;text-align:center}
.sig-three .name{font-size:13px}
.sig-three .role{font-size:9px}
.sig-three .addr{position:absolute;left:226px;top:27px;font-size:9px;line-height:11.5px}
.sig-three .contact-list{position:absolute;left:348px;top:27px;font-size:9px;line-height:11.5px}
.sig-three .icon{width:6.5px;height:6.5px}
</style>
</head>
<body>

<svg width="0" height="0" style="position:absolute" aria-hidden="true">
  <defs>
    <symbol id="i-phone" viewBox="0 0 10 10"><path d="M2 0.5l2 2-1 1.2c.6 1.3 1.6 2.3 2.9 2.9l1.2-1 2 2-1.3 1.6C4.5 9.2.8 5.5.4 1.8z"/></symbol>
    <symbol id="i-mobile" viewBox="0 0 10 10"><path d="M2.8 0h4.4c.5 0 .8.3.8.8v8.4c0 .5-.3.8-.8.8H2.8c-.5 0-.8-.3-.8-.8V.8c0-.5.3-.8.8-.8zM3.2 1.2v6.6h3.6V1.2z"/></symbol>
    <symbol id="i-mail" viewBox="0 0 10 10"><path d="M0 2h10v6H0zM.8 2.6L5 5.6l4.2-3H.8z"/></symbol>
    <symbol id="i-globe" viewBox="0 0 10 10"><circle cx="5" cy="5" r="4.6"/><path d="M2.2 4h5.6v.8H2.2zM2.2 5.8h5.6v.8H2.2z" fill="#fff" opacity=".6"/></symbol>
  </defs>
</svg>

<!-- Letterhead -->
<section class="piece letterhead">
  <div class="soft-fade" style="left:130px;top:330px;width:260px;height:222px"></div>
  <div class="pennant">
    <svg class="shape" viewBox="0 0 89 113" preserveAspectRatio="none"><polygon points="0,0 89,0 89,84 0,113" fill="var(--ink)"/></svg>
    <span class="brand-name">VALE 8</span>
  </div>
  <div class="lh-address">
    <div>4120 Laurel Court</div>
    <div>Juneau, Alaska 34810</div>
    <ul class="contact-list">
      <li><svg class="icon"><use href="#i-phone"/></svg>555-204-7731</li>
      <li><svg class="icon"><use href="#i-mobile"/></svg>555-318-6642</li>
      <li><svg class="icon"><use href="#i-mail"/></svg>info@vale8.com</li>
      <li><svg class="icon"><use href="#i-globe"/></svg>www.vale8.com</li>
    </ul>
  </div>
  <p class="salutation">Dear Mr. Carter,</p>
  <div class="letter-body">
    <p>Lorem ipsum dolor sit amet, consectetur adipiscing elit. Donec orci purus, luctus vitae dignissim eu, iaculis sed purus. Vivamus faucibus, ipsum nec aliquet viverra, leo mauris condimentum ligula, sit amet sagittis enim ligula quis arcu. Nam egestas tortor id nisi porttitor mattis. In tortor ante, ultricies in suscipit a, tempus non massa. Vivamus et auctor mi. Fusce vel massa nulla. Phasellus nec eros mauris, et scelerisque orci.</p>
    <p>Donec malesuada orci vitae nulla accumsan porta a id massa. Quisque accumsan iaculis magna sit amet fringilla. Maecenas consequat, magna eget tincidunt semper, odio nibh rutrum mi, id feugiat ante nisi eu risus. Vestibulum nunc orci, rhoncus a placerat in, ultricies in mi. Cras mattis varius eros, vel fringilla nisi suscipit eget. Quisque scelerisque sagittis nulla at porttitor.</p>
    <p>Sed id augue vitae urna euismod commodo aliquet a quam. Pellentesque arcu velit, cursus et malesuada ut, consequat et diam. Nullam erat sem, rhoncus id ullamcorper vitae, rhoncus et arcu. In ultricies ultricies nulla, ut rutrum nisi iaculis at. Donec eu magna a metus ornare faucibus. Fusce aliquet faucibus ultricies. Morbi semper, est id tincidunt gravida, sem arcu adipiscing lacus, ac bibendum nulla leo eu purus. Quisque nec diam sed risus consectetur accumsan quis quis nibh. Vestibulum id purus lorem.</p>
    <p>It is a long established fact that a reader will be distracted by the readable content of a page when looking at its layout. The point of using Lorem Ipsum is that it has a more-or-less normal distribution of letters, as opposed to using 'Content here, content here', making it look like readable English. Many desktop publishing packages</p>
  </div>
  <p class="signoff">Sincerely,</p>
  <div class="signature" role="img" aria-label="Handwritten signature of Daniel Hart"></div>
  <p class="tagline script">Build Lasting Wealth With Care</p>
</section>
<p class="label" style="left:268px;top:619px">LETTERHEAD</p>

<!-- Envelope -->
<section class="piece env-back">
  <div class="env-flap">
    <svg viewBox="0 0 354 58" width="354" height="58" aria-hidden="true"><path d="M0 0H354L347 36Q344 58 322 58H32Q10 58 7 36Z" fill="var(--blue)"/></svg>
    <span class="brand-name">VALE 8</span>
    <span class="tagline script">Build Lasting Wealth With Care</span>
  </div>
</section>
<section class="piece env-front">
  <div class="soft-fade" style="left:200px;top:40px;width:156px;height:121px"></div>
  <div class="pennant">
    <svg class="shape" viewBox="0 0 71 83" preserveAspectRatio="none"><polygon points="0,0 71,0 71,61 0,83" fill="var(--ink)"/></svg>
    <span class="brand-name">VALE 8</span>
  </div>
  <div class="env-address">
    <div>4120 Laurel Court</div>
    <div>Juneau, Alaska 34810</div>
  </div>
</section>
<p class="label" style="left:723px;top:302px">ENVELOPE</p>

<!-- Business cards -->
<section class="piece card-front">
  <div class="cf-info">
    <div class="cf-name">
      <strong>DANIEL HART</strong>
      <div>President</div>
      <div>4120 Laurel Court</div>
      <div>Juneau, Alaska 34810</div>
    </div>
    <ul class="contact-list">
      <li><svg class="icon"><use href="#i-phone"/></svg>555-204-7731</li>
      <li><svg class="icon"><use href="#i-mobile"/></svg>555-462-1190</li>
      <li><svg class="icon"><use href="#i-mail"/></svg>info@vale8.com</li>
      <li><svg class="icon"><use href="#i-globe"/></svg>www.vale8.com</li>
    </ul>
  </div>
</section>
<p class="label" style="left:1039px;top:163px">FRONT CARD</p>

<section class="piece card-back">
  <span class="brand-name">VALE 8</span>
  <span class="tagline script">Build Lasting Wealth With Care</span>
</section>
<p class="label" style="left:1039px;top:302px">BACK CARD</p>

<!-- Email signature 1 -->
<section class="piece sig sig-one">
  <div class="dark-fade" style="left:40px;top:150px;width:135px;height:116px"></div>
  <span class="brand-name">VALE 8</span>
  <span class="name">Daniel Hart</span>
  <span class="role">President</span>
  <span class="rule" style="top:145px"></span>
  <div class="addr"><div>4120 Laurel Court</div><div>Juneau, Alaska 34810</div></div>
  <span class="rule" style="top:184px"></span>
  <ul class="contact-list">
    <li><svg class="icon"><use href="#i-phone"/></svg>555-204-7731</li>
    <li><svg class="icon"><use href="#i-mobile"/></svg>555-318-6642</li>
    <li><svg class="icon"><use href="#i-mail"/></svg>info@vale8.com</li>
    <li><svg class="icon"><use href="#i-globe"/></svg>www.vale8.com</li>
  </ul>
</section>
<p class="label" style="left:577px;top:619px">EMAIL SIGNATURE 1</p>

<!-- Email signature 2 -->
<section class="piece sig sig-two">
  <div class="dark-fade" style="left:290px;top:20px;width:165px;height:121px"></div>
  <span class="brand-name">VALE 8</span>
  <span class="vr" style="left:138px;top:48px;height:49px"></span>
  <span class="name">Daniel Hart</span>
  <span class="role">President</span>
  <div class="addr"><div>4120 Laurel Court</div><div>Juneau, Alaska 34810</div></div>
  <span class="vr" style="left:295px;top:48px;height:49px"></span>
  <ul class="contact-list">
    <li><svg class="icon"><use href="#i-phone"/></svg>555-204-7731</li>
    <li><svg class="icon"><use href="#i-mobile"/></svg>555-318-6642</li>
    <li><svg class="icon"><use href="#i-mail"/></svg>info@vale8.com</li>
    <li><svg class="icon"><use href="#i-globe"/></svg>www.vale8.com</li>
  </ul>
</section>
<p class="label" style="left:922px;top:486px">EMAIL SIGNATURE 2</p>

<!-- Email signature 3 -->
<section class="piece sig sig-three">
  <div class="dark-fade" style="left:320px;top:10px;width:135px;height:77px"></div>
  <span class="brand-name">VALE 8</span>
  <span class="vr" style="left:101px;top:29px;height:32px"></span>
  <div class="who"><div class="name">Daniel Hart</div><div class="role">President</div></div>
  <span class="vr" style="left:212px;top:29px;height:32px"></span>
  <div class="addr"><div>4120 Laurel Court</div><div>Juneau, Alaska 34810</div><div>www.vale8.com</div></div>
  <span class="vr" style="left:334px;top:29px;height:32px"></span>
  <ul class="contact-list">
    <li><svg class="icon"><use href="#i-phone"/></svg>555-204-7731</li>
    <li><svg class="icon"><use href="#i-mobile"/></svg>555-318-6642</li>
    <li><svg class="icon"><use href="#i-mail"/></svg>info@vale8.com</li>
  </ul>
</section>
<p class="label" style="left:922px;top:619px">EMAIL SIGNATURE 3</p>

</body>
</html>
```